Company Website for Varnoth Signal, an open source data analytics company focused on relationship and li

I need a company/brand website for our new startup, Varnoth Signal LLC. We are a company focused on using life pattern analysis techniques, looking at relationships and how relationships, attributes, and activity cluster to infer aggregate information about individuals and groups. Our focus is on improving the digital advertising market.

We have a company logo which I will upload shortly.

Target Market(s)

Digital Advertising

Number of Pages Required

3 page

Font styles to use
Sans Serif

Requirements
Must have
• An main page, about us, contact page.
Nice to have
• Varnoth Signal relies on state of the art analytics applied to a the digital marketing space. While it is heavy in science, we also understand the art of influence. The website should have a scientific edge but also a flair that illustrates our focus on applying the hard science and analytics to influencing the behavior of people.

```html
<!DOCTYPE html>
<html lang="en">
<head>
<meta charset="utf-8">
<title>Varnoth Signal</title>
<link href="https://fonts.googleapis.com/css2?family=Montserrat:wght@500;600;700;800&family=Roboto:wght@400;500;700&display=swap" rel="stylesheet">
<style>
:root{
  --orange:#f08a24;
  --orange-dark:#e07a14;
  --navy:#0d2a4a;
  --navy-deep:#081c35;
  --blue:#2a93dc;
  --ink:#1b1b1b;
  --muted:#6d6d6d;
  --line:#e2e2e2;
  --paper:#ffffff;
  --mist:#f3f4f6;
  --footer:#121417;
  --footer-text:#c9c9c9;
}
*{box-sizing:border-box;margin:0;padding:0}
html,body{width:1200px;height:3523px;overflow:hidden}
body{font-family:"Roboto",Arial,sans-serif;color:var(--ink);background:var(--paper);position:relative}
.abs{position:absolute}
.heading{font-family:"Montserrat",Arial,sans-serif;font-weight:800;text-transform:uppercase;letter-spacing:1px}
.ghost{font-family:"Montserrat",Arial,sans-serif;font-weight:800;text-transform:uppercase;color:rgba(0,0,0,.05);font-size:74px;letter-spacing:2px;white-space:nowrap}
.center{left:0;width:1200px;text-align:center}
.lede{font-size:13px;line-height:23px;color:var(--muted)}
.btn{display:flex;align-items:center;justify-content:center;gap:6px;font-family:"Montserrat",Arial,sans-serif;font-weight:700;font-size:13px;text-transform:uppercase;height:40px}
.btn-outline{border:1.5px solid var(--orange);color:var(--orange);background:#fff}
.btn-solid{background:var(--orange);color:#fff}
.btn-white{border:2px solid #fff;color:#fff}
.dot{width:14px;height:14px;border-radius:50%;background:currentColor;display:inline-flex;align-items:center;justify-content:center}
.dot svg{width:8px;height:8px}

/* header */
.topline{top:0;left:0;width:1200px;height:4px;background:var(--orange)}
.brand{top:34px;left:99px;font-family:"Montserrat",Arial,sans-serif;font-weight:800;font-size:24px;color:var(--blue);display:flex;align-items:center;gap:8px}
.brand i{width:12px;height:12px;background:var(--orange);border-radius:50%;display:block}
.nav{top:46px;left:545px;display:flex;gap:22px;font-family:"Montserrat",Arial,sans-serif;font-weight:700;font-size:14px;color:#222}

/* hero */
.hero{top:118px;left:0;width:1200px;height:516px;background:radial-gradient(ellipse at 55% 55%,#1a3f66 0%,var(--navy) 45%,var(--navy-deep) 100%)}
.hero-title{top:248px;font-size:50px;color:#fff;letter-spacing:4px}
.hero-sub{top:320px;color:#fff;font-size:15px;line-height:26px}
.hero-btn{top:400px;left:507px;width:186px;height:46px;font-size:15px;font-weight:600}

/* what we do */
.wwd-ghost{top:690px}
.wwd-title{top:720px;font-size:34px}
.wwd-lede{top:776px}
.feature{top:857px;width:310px;height:305px;text-align:center}
.feature.raised{background:#fff;box-shadow:0 2px 10px rgba(0,0,0,.12)}
.feature .icon{width:86px;height:86px;border-radius:50%;margin:0 auto;background:radial-gradient(circle,#e8f2fb 0%,#f7f7f7 70%);border:1px solid var(--line)}
.feature h3{font-family:"Montserrat",Arial,sans-serif;font-weight:700;font-size:21px;text-transform:uppercase;margin-top:26px}
.feature p{font-size:13px;line-height:23px;color:var(--muted);margin-top:10px}
.feature .btn{width:148px;margin:20px auto 0}

/* life pattern */
.life-photo{top:1252px;left:0;width:599px;height:429px;background:linear-gradient(135deg,#c9c3b6 0%,#8a8f96 45%,#4f6f8c 100%)}
.life-panel{top:1252px;left:599px;width:601px;height:429px;background:var(--blue)}
.life-title{top:1305px;left:664px;width:480px;color:#fff;font-size:32px;line-height:46px}
.life-text{top:1415px;left:664px;width:440px;color:#fff;font-size:12.5px;line-height:24px}
.life-btn{top:1575px;left:664px;width:158px}

/* why choose */
.why-ghost{top:1740px}
.why-title{top:1772px;font-size:30px}
.why-card{top:1843px;width:305px;height:392px;background:#fff;box-shadow:0 2px 10px rgba(0,0,0,.15);text-align:center;padding:6px}
.why-card .photo{height:188px}
.why-card h3{font-family:"Montserrat",Arial,sans-serif;font-weight:700;font-size:19px;text-transform:uppercase;margin-top:38px}
.why-card p{font-size:13px;line-height:23px;color:var(--muted);margin-top:20px}
.why-card .btn{width:148px;margin:16px auto 0}

/* orange band */
.band{top:2343px;left:0;width:1200px;height:404px;background:linear-gradient(90deg,var(--orange) 0%,#f3963a 50%,var(--orange) 100%)}
.band-title{top:2410px;color:#fff;font-size:32px;line-height:46px}
.band-text{top:2522px;left:200px;width:800px;text-align:center;color:#fff;font-size:12.5px;line-height:24px}
.band-btn{top:2631px;left:501px;width:198px;height:46px}

/* clients */
.clients-ghost{top:2812px}
.clients-title{top:2844px;font-size:32px}
.clients-lede{top:2898px}
.client{top:2982px;width:174px;height:82px;border:1px solid #cfcfcf;background:#fff;display:flex;align-items:center;justify-content:center;gap:8px;font-family:"Montserrat",Arial,sans-serif;font-weight:800;font-size:21px;color:#2a2a2a;text-transform:uppercase}
.client i{width:12px;height:12px;background:#2a2a2a;display:block}
.arrow{top:3008px}

/* footer */
.footer{top:3170px;left:0;width:1200px;height:353px;background:radial-gradient(ellipse at 70% 30%,#1d2329 0%,var(--footer) 70%)}
.f-brand{top:3280px;left:99px;font-family:"Montserrat",Arial,sans-serif;font-weight:800;font-size:26px;color:var(--blue);line-height:32px}
.f-col{top:3236px}
.f-col h4{font-family:"Montserrat",Arial,sans-serif;font-weight:700;font-size:15px;color:#fff;text-transform:uppercase;margin-bottom:14px}
.f-col li{list-style:none;font-size:12.5px;color:var(--footer-text);line-height:24.6px;display:flex;align-items:center;gap:9px}
.f-col li::before{content:"»";color:#fff;font-size:13px}
.f-rule{top:3444px;left:99px;width:1002px;height:1px;background:#3a3f45}
.copy{top:3474px;left:99px;font-size:12.5px;color:#e6e6e6}
.social{top:3464px;width:36px;height:36px;border:1.5px solid #bfbfbf;border-radius:50%}
</style>
</head>
<body>

<div class="abs topline"></div>
<div class="abs brand"><i></i>Varnoth Signal</div>
<nav class="abs nav">
  <span>HOME</span><span>SERVICES</span><span>WORK</span><span>SOLUTIONS</span><span>COMMUNITY</span><span>CONTACT</span>
  <svg width="16" height="16" viewBox="0 0 16 16"><circle cx="6.5" cy="6.5" r="4.5" fill="none" stroke="#222" stroke-width="2"/><line x1="10" y1="10" x2="14" y2="14" stroke="#222" stroke-width="2.4"/></svg>
</nav>

<section class="abs hero" role="img" aria-label="Dark navy backdrop with flowing orange data wave lines and connected points"></section>
<h1 class="abs center heading hero-title">Varnoth Signal</h1>
<p class="abs center hero-sub">Nemo enim ipsam voluptatem quia voluptas sit aspernatur aut odit autsed<br>quia consequuntur magni dolores eos qui ratione</p>
<div class="abs btn btn-white hero-btn">Read More <span class="dot" style="color:#fff"><svg viewBox="0 0 8 8"><path d="M2.5 1l3 3-3 3" fill="none" stroke="#0d2a4a" stroke-width="1.6"/></svg></span></div>
<svg class="abs" style="top:355px;left:40px" width="22" height="34" viewBox="0 0 22 34"><path d="M18 2L4 17l14 15" fill="none" stroke="#fff" stroke-width="3"/></svg>
<svg class="abs" style="top:355px;left:1138px" width="22" height="34" viewBox="0 0 22 34"><path d="M4 2l14 15L4 32" fill="none" stroke="#fff" stroke-width="3"/></svg>
<svg class="abs" style="top:536px;left:586px" width="28" height="60" viewBox="0 0 28 60"><rect x="2" y="2" width="24" height="36" rx="12" fill="none" stroke="#fff" stroke-width="2"/><line x1="14" y1="9" x2="14" y2="16" stroke="#fff" stroke-width="2"/><line x1="14" y1="42" x2="14" y2="56" stroke="#fff" stroke-width="2"/><path d="M9 51l5 5 5-5" fill="none" stroke="#fff" stroke-width="2"/></svg>

<div class="abs center ghost wwd-ghost">What We Do</div>
<h2 class="abs center heading wwd-title">What We Do</h2>
<p class="abs center lede wwd-lede">Lorem ipsum dolor sit amet, consectetur adipiscing elit, sed do eiusmod tempor incididunt ut labore et dolore<br>magna aliqua. Ut enim ad minim veniam, quis nostrud exercitation ullamco laboris.</p>

<div class="abs feature" style="left:99px">
  <div class="icon" role="img" aria-label="Pattern analysis icon"></div>
  <h3>Pattern Analysis</h3>
  <p>Lorem ipsum dolor sit consectetur<br>adipi scing do eiusmod tempor incididunt ut<br>labore et dolore magna aliqua.</p>
  <div class="btn btn-outline">Read More <span class="dot"><svg viewBox="0 0 8 8"><path d="M2.5 1l3 3-3 3" fill="none" stroke="#fff" stroke-width="1.6"/></svg></span></div>
</div>
<div class="abs feature raised" style="left:446px;padding-top:0">
  <div class="icon" role="img" aria-label="Faster access icon"></div>
  <h3>Faster Access</h3>
  <p>Lorem ipsum dolor sit consectetur<br>adipi scing do eiusmod tempor incididunt ut<br>labore et dolore magna aliqua.</p>
  <div class="btn btn-solid">Read More <span class="dot" style="color:#fff"><svg viewBox="0 0 8 8"><path d="M2.5 1l3 3-3 3" fill="none" stroke="#f08a24" stroke-width="1.6"/></svg></span></div>
</div>
<div class="abs feature" style="left:791px">
  <div class="icon" role="img" aria-label="Greater innovation icon"></div>
  <h3>Greater Innovation</h3>
  <p>Lorem ipsum dolor sit consectetur<br>adipi scing do eiusmod tempor incididunt ut<br>labore et dolore magna aliqua.</p>
  <div class="btn btn-outline">Read More <span class="dot"><svg viewBox="0 0 8 8"><path d="M2.5 1l3 3-3 3" fill="none" stroke="#fff" stroke-width="1.6"/></svg></span></div>
</div>

<div class="abs life-photo" role="img" aria-label="Two colleagues reviewing analytics on a desktop monitor"></div>
<div class="abs life-panel"></div>
<h2 class="abs heading life-title">Life Pattern Analysis Techniques</h2>
<p class="abs life-text">Lorem ipsum dolor sit amet, consectetur adipiscing elit, sed do eiusmod tempor incididunt ut labore et dolore magna aliqua. Ut enim ad minim veniam, quis nostrud exercitation ullamco laboris nisi ut aliquip ex ea com modo consequat. Duis aute irure dolor in reprehenderit in voluptate velit esse cillum dolore eu fugiat nulla pariatur.</p>
<div class="abs btn btn-white life-btn">Read More <span class="dot" style="color:#fff"><svg viewBox="0 0 8 8"><path d="M2.5 1l3 3-3 3" fill="none" stroke="#2a93dc" stroke-width="1.6"/></svg></span></div>

<div class="abs center ghost why-ghost">Why Choose Us?</div>
<h2 class="abs center heading why-title">Why Choose Us?</h2>

<div class="abs why-card" style="left:101px">
  <div class="photo" role="img" aria-label="Group of people talking together in a circle" style="background:linear-gradient(135deg,#8a6a4c,#c79b6a 50%,#5b4a3c)"></div>
  <h3>Scientific Edge</h3>
  <p>Lorem ipsum dolor sit consectetur<br>adipi scing do eiusmod tempor incididunt ut<br>labore et dolore magna aliqua.</p>
  <div class="btn btn-outline">Read More <span class="dot"><svg viewBox="0 0 8 8"><path d="M2.5 1l3 3-3 3" fill="none" stroke="#fff" stroke-width="1.6"/></svg></span></div>
</div>
<div class="abs why-card" style="left:448px">
  <div class="photo" role="img" aria-label="Tablet displaying charts held in hands" style="background:linear-gradient(135deg,#3a3a3a,#d9d9d9 50%,#e8a060)"></div>
  <h3>Hard Science</h3>
  <p>Lorem ipsum dolor sit consectetur<br>adipi scing do eiusmod tempor incididunt ut<br>labore et dolore magna aliqua.</p>
  <div class="btn btn-outline">Read More <span class="dot"><svg viewBox="0 0 8 8"><path d="M2.5 1l3 3-3 3" fill="none" stroke="#fff" stroke-width="1.6"/></svg></span></div>
</div>
<div class="abs why-card" style="left:796px">
  <div class="photo" role="img" aria-label="Glowing green and blue data waves on a dark background" style="background:linear-gradient(160deg,#07101f,#0f5b3a 55%,#1a2f7a)"></div>
  <h3>Influence Analytics</h3>
  <p>Lorem ipsum dolor sit consectetur<br>adipi scing do eiusmod tempor incididunt ut<br>labore et dolore magna aliqua.</p>
  <div class="btn btn-outline">Read More <span class="dot"><svg viewBox="0 0 8 8"><path d="M2.5 1l3 3-3 3" fill="none" stroke="#fff" stroke-width="1.6"/></svg></span></div>
</div>

<section class="abs band" role="img" aria-label="Orange tinted photo of a team meeting"></section>
<h2 class="abs center heading band-title">Open Source Data Analytics For<br>Relationship And Lifestyle</h2>
<p class="abs band-text">Lorem ipsum dolor sit amet, consectetur adipiscing elit, sed do eiusmod tempor incididunt ut labore et dolore magna aliqua. Ut enim veniam, quis nostrud exercitation ullamco laboris nisi ut aliquip ex ea commodo consequat. Duis aute irure dolor in reprehenderit in voluptate velit esse cillum dolore eu fugiat nulla pariatur. Excepteur sint occaecat cupidatat non proident</p>
<div class="abs btn btn-white band-btn">Get Started Now <span class="dot" style="color:#fff"><svg viewBox="0 0 8 8"><path d="M2.5 1l3 3-3 3" fill="none" stroke="#f08a24" stroke-width="1.6"/></svg></span></div>

<div class="abs center ghost clients-ghost">Our Clients</div>
<h2 class="abs center heading clients-title">Our Clients</h2>
<p class="abs center lede clients-lede">Lorem ipsum dolor sit amet, consectetur adipiscing elit, sed do eiusmod tempor incididunt ut labore et dolore<br>magna aliqua. Ut enim ad minim veniam nostrud exercitation ullamco laboris nisi ut aliquip.</p>
<svg class="abs arrow" style="left:58px" width="16" height="26" viewBox="0 0 16 26"><path d="M13 2L3 13l10 11" fill="none" stroke="#555" stroke-width="2.4"/></svg>
<div class="abs client" style="left:101px"><i></i>Ironmill</div>
<div class="abs client" style="left:306px">Kestrel</div>
<div class="abs client" style="left:512px">Slateform</div>
<div class="abs client" style="left:718px">Plume Co</div>
<div class="abs client" style="left:924px">Tallow</div>
<svg class="abs arrow" style="left:1126px" width="16" height="26" viewBox="0 0 16 26"><path d="M3 2l10 11L3 24" fill="none" stroke="#555" stroke-width="2.4"/></svg>

<footer class="abs footer" role="img" aria-label="Dark background with faint network lines"></footer>
<div class="abs f-brand">Varnoth<br>Signal</div>
<div class="abs f-col" style="left:352px"><h4>Quick Links</h4><ul><li>Home</li><li>About Us</li><li>Services</li><li>Solution</li><li>Contact Us</li></ul></div>
<div class="abs f-col" style="left:540px"><h4>Resources</h4><ul><li>Analysis Techniques</li><li>Looking At Relationships</li><li>How Relationships</li><li>Attributes</li><li>Activity Cluster</li></ul></div>
<div class="abs f-col" style="left:777px"><h4>Our Focus</h4><ul><li>Scientific Edge</li><li>Hard Science</li><li>Analytics Influence</li><li>Behavior Of People</li></ul></div>
<div class="abs f-col" style="left:979px"><h4>Support</h4><ul><li>Help</li><li>FAQs</li><li>Privacy Policy</li><li>Terms Of Service</li></ul></div>
<div class="abs f-rule"></div>
<p class="abs copy">Copyrights © 2018 Varnoth Signal. All Rights Reserved.</p>
<div class="abs social" style="left:909px"></div>
<div class="abs social" style="left:959px"></div>
<div class="abs social" style="left:1010px"></div>
<div class="abs social" style="left:1062px"></div>

</body>
</html>
```